Etiketten für Imkerei mit Spezialisierung auf Bio Lagenhonig
Zielgruppe
wiesfalter.at - BioImkerei Lindorf
Kleine Nebenerwerbs Imkerei mit Spezialisierung auf Bio Lagenhonig (nähere Infos sind auf der Website nachzulesen)
Als weitere Produktlinie bieten wir Honig+ / Honig mit Zutaten wie Himbeer, Erdbeer, Haselnuss, Mohn, Ingwer, Thymian, usw an.
Zielgruppe: Personen die offen für die Vielfalt der Natur sind, gesunde und natürliche Lebensmittel lieben und die bereit sind die aufwändige, großteils manuelle, Arbeit entsprechend zu entlohnen.
Gesucht:
ÄNDERUNG: Da die Anforderung für das ausgesetzte Preisgeld offensichtlich zu komplex ist, reduziere ich die Anforderung auf Etiketten für die Produktserie Honig+, Gesamtkonzepte sind nicht erforderlich werden aber gerne angenommen.
ÜRSPRÜNGLICH:
Redesign der aktuellen Honigetiketten
Basisdesign für Lagenhonig und Honig+ das entsprechende Varianten zulässt.
Aufgabenstellung
Ich wünsche mir ein modernes, edles (oder Öko look) Design mit sehr guten Wiedererkennungswert das sich von gängigen Honigetiketten deutlich abhebt.
Das wiesfalter Logo soll enthalten sein kann aber bei Bedarf angepasst werden (z.B. monocrome Verison)
Für Lagenhonig werden derzeit 400g und 100g Gläser mit hohem schwarzen DrehKap Decke und,
für Honig+ 250g und 100g mit hohem silbenen DrehKap Deckel verwendet. Beispiele sind im Webshop unter https://solvenhof.at/index.php/wiesfalter ersichtilich.
Für das Ablaufdatum ist evtl. ein Feld für manuelle Stempelung vorzusehen.
Bitte die Sichtfeldregelung der EU Verpackungsverordnung einhalten.
Bisherige Etiketten hatten den Anspruch das diese auf guten Laserdruckern ausdruckbar waren - das ist jetzt nicht mehr zwingend notwendig (wäre für Kleinauflagen aber trotzdem vorteilhaft)

```html
<!DOCTYPE html>
<html lang="de">
<head>
<meta charset="utf-8">
<title>Honig+ Etikett – Johannisbeere</title>
<link rel="stylesheet" href="https://fonts.googleapis.com/css2?family=Source+Sans+3:wght@400;700&family=Roboto+Condensed:wght@400;700&display=swap">
<style>
  :root {
    --page: #f4f1ec;
    --label-white: #f3f3f3;
    --ink-brown: #4a3b31;
    --ink-grey: #4d4d4d;
    --bio-green: #8cb820;
    --bio-green-light: #b5d04a;
    --honey-deep: #f3a712;
    --honey-light: #fbd98a;
    --on-honey: #ffffff;
  }
  * { margin: 0; padding: 0; box-sizing: border-box; }
  html, body { width: 1180px; height: 1200px; overflow: hidden; }
  body {
    background: var(--page);
    font-family: "Source Sans 3", sans-serif;
    position: relative;
  }
  .label-strip {
    position: absolute;
    left: 60px; top: 220px;
    width: 1060px; height: 760px;
    display: flex;
  }
  .front-panel {
    position: relative;
    width: 740px; height: 100%;
    background: linear-gradient(90deg, #fafafa 0%, var(--label-white) 60%, #e9e9e9 100%);
    padding: 22px 26px 0 26px;
    color: var(--ink-grey);
  }
  .product-title {
    font-weight: 700;
    font-size: 44px;
    line-height: 1.05;
    color: var(--ink-brown);
  }
  .product-subtitle {
    font-size: 29px;
    line-height: 1.2;
    margin-top: 6px;
  }
  .section-heading {
    font-weight: 700;
    font-size: 29px;
    color: var(--ink-brown);
    margin-top: 36px;
  }
  .ingredients {
    font-size: 26px;
    line-height: 1.2;
    margin-top: 4px;
  }
  .ingredients-note {
    font-size: 21px;
    line-height: 1.3;
    margin-top: 2px;
  }
  .storage-note {
    font-size: 23px;
    line-height: 1.12;
    margin-top: 22px;
  }
  .organic-badge {
    position: absolute;
    left: 26px; top: 492px;
    width: 370px; height: 246px;
    background: linear-gradient(90deg, var(--bio-green-light) 0%, var(--bio-green) 100%);
  }
  .organic-info {
    position: absolute;
    left: 415px; top: 500px;
    color: #333;
  }
  .control-code { font-size: 34px; line-height: 1.05; }
  .origin { font-size: 26px; line-height: 1.05; color: var(--ink-grey); }
  .bio-word {
    font-size: 96px;
    line-height: 0.95;
    color: var(--bio-green);
    margin-top: 2px;
  }
  .net-weight { font-size: 50px; line-height: 1.1; margin-top: 2px; color: #222; }
  .back-panel {
    position: relative;
    flex: 1;
    background: linear-gradient(90deg, var(--honey-deep) 0%, #f8c24a 55%, var(--honey-light) 100%);
    color: var(--on-honey);
    font-family: "Roboto Condensed", sans-serif;
    padding: 178px 0 0 24px;
  }
  .producer-name { font-weight: 700; font-size: 32px; line-height: 1.2; }
  .producer-address { font-size: 28px; line-height: 1.4; }
  .producer-web { font-weight: 700; font-size: 30px; margin-top: 36px; }
  .best-before {
    position: absolute;
    left: 24px; top: 664px;
    font-size: 23px;
    line-height: 1.3;
  }
  .stamp-field {
    position: absolute;
    right: 40px; top: 650px;
  }
</style>
</head>
<body>
  <div class="label-strip">
    <section class="front-panel">
      <h1 class="product-title">Honigkomposition</h1>
      <p class="product-subtitle">mit österreichischem Blütenhonig<br>aus biologischer Bienenhaltung</p>

      <h2 class="section-heading">Zutaten</h2>
      <p class="ingredients">95% Blütenhonig aus kontrolliert<br>biologischer Landwirtschaft,<br>5% Johannisbeerpulver</p>
      <p class="ingredients-note">(gefriergetrocknet,<br>entspricht 45% Frischfruchtanteil)</p>

      <p class="storage-note">vor Wärme geschützt<br>und trocken lagern</p>

      <div class="organic-badge" role="img" aria-label="Bio-Siegel"></div>

      <div class="organic-info">
        <p class="control-code">AT-BIO-000</p>
        <p class="origin">EU-Landwirtschaft</p>
        <p class="bio-word">BIO</p>
        <p class="net-weight">400 g</p>
      </div>
    </section>

    <section class="back-panel">
      <p class="producer-name">Bio Imkerei Lindorf</p>
      <p class="producer-address">Ahornweg 12<br>3594 Talbach</p>
      <p class="producer-web">www.wiesfalter.at</p>

      <p class="best-before">Mindestens<br>haltbar bis:</p>
      <svg class="stamp-field" width="160" height="90" viewBox="0 0 160 90" aria-hidden="true">
        <polygon points="0,90 160,0 160,90" fill="#ffffff"/>
      </svg>
    </section>
  </div>
</body>
</html>
```